July 2022 Industrial Manufacturer Product Expo Mexico City

We manufacture large screws and fastners for large Mining equipment, Trains, large ships, airplanes, wind turbines, and so on. We also do custom work base on the customer needs. No matter the size we can make it.
We have a Expo coming up with companies all over the world. We have to stand out we are a family own business so our customer service will be above and beyond anyone can provide. We do not have a sales force to push our products and services we provide one on one service.
Plus@!! I'm looking for anything that you designers can come up with if it was your company to put on a business card, plus i want to do a 1 or 2 sided pamphlet, and then a website. We make Speciality Bolts for large mining equipment these bolts can be 3 to 4 foot long!!! Plus fasteners, Nuts, washers, any, size, strengths, special materials, we offer more of a ono on one customer service, We are a small company, family own, but can fulfill any type of orders. We can also provide special time lines for emergency orders. "We keep the machines running we here at KRV don't believe in down time" We want to hear any slogan based on our company to stand out.
Thanks i really appreciate all your work and options that we have to pick on. Plus just a thought we could possibly want to entertain a experience Marketing internet help maybe a employment possibility. Thanks

I need 2 cards one in Spanish and English Like the steel back ground maybe send me in some bright red and blue writing Same with the Black cards Please remove the word Military The logo KRV maybe integrate a picture of a Bolt 🔩 Thank you

Still looking for I need 2 cards one in Spanish and English Like the steel back ground maybe send me in some bright red and blue writing Same with the Black cards try bright writing Please remove the word Military The logo KRV maybe integrate a picture of a Bolt 🔩 Plus will need the company to make a brochure and website next Thank you

Target Market(s)

Large Mining, Ship, Train, Green Energy, VELM, and Government equipment. Throughout the World

Industry/Entity Type

We can Custom Manufacture any type of Fastners for Mining equipment, Trains, Ships, Green energy, Governments, or military projects. wind turbines,

Contact Information for Business Card

I attached the name and contact info that's on a card, plus the Company Logo. Would like industrial looking background with Bright Colors that will stand out!! If we can insert somewhere maybe on back that we "Custom Manufacture Any Size or Quantity Fastners for Large Mining Equipment, Trains, Ships, Green Energy Equipment or Government Projects

Font styles to use
Other font styles liked:
• You Pick, has to be bold, colorful standout, Professional looking Beable to read it.

Colors

Designer to choose colors to be used in the design.

Requirements
Must have
• Need in Spanish and English TO STANDOUT FROM THE REST OF THE EXPO!! See Business card details, Rounded corners
Nice to have
• Can i see some of the darker cards with Bright Red and Blue letters I like to see the different type of card material, heavy thickness, plastic, transparent, Metal types, Bright Colors, I saw like Raised letters like on the logo.

```html
<!DOCTYPE html>
<html lang="es">
<head>
<meta charset="utf-8">
<title>KRV Business Card</title>
<link rel="stylesheet" href="https://fonts.googleapis.com/css2?family=Source+Sans+3:wght@400;600&display=swap">
<style>
  :root {
    --page-bg: #e9e7e6;
    --top-light: #f4f1f1;
    --top-shade: #ddd6d6;
    --logo-grey: #3b3b3e;
    --dark-left: #6b6b6e;
    --dark-right: #000000;
    --rule-grey: #8a8a8c;
    --name-blue: #1a98dc;
    --text-white: #ffffff;
    --band-light: #0096d9;
    --band-deep: #0b2784;
  }
  * { margin: 0; padding: 0; box-sizing: border-box; }
  html, body {
    width: 1200px;
    height: 900px;
    overflow: hidden;
    background: var(--page-bg);
    font-family: "Source Sans 3", sans-serif;
  }
  .canvas {
    width: 1200px;
    height: 900px;
    display: flex;
    align-items: center;
    justify-content: center;
  }
  .business-card {
    width: 1000px;
    height: 618px;
    border-radius: 18px;
    overflow: hidden;
    display: flex;
    flex-direction: column;
    box-shadow: 0 10px 30px rgba(0,0,0,0.18);
  }
  .card-header {
    height: 229px;
    background: radial-gradient(ellipse at 50% 40%, var(--top-light) 0%, var(--top-shade) 100%);
    display: flex;
    align-items: center;
    justify-content: center;
    gap: 22px;
  }
  .brand-mark {
    width: 34px;
    height: 34px;
    border-radius: 50%;
    background: var(--band-light);
  }
  .brand-name {
    font-size: 132px;
    font-weight: 600;
    letter-spacing: 10px;
    line-height: 1;
    color: var(--logo-grey);
  }
  .contact-panel {
    height: 250px;
    background: linear-gradient(100deg, var(--dark-left) 0%, #3a3a3c 30%, #111 60%, var(--dark-right) 100%);
    display: flex;
    flex-direction: column;
    align-items: center;
    padding-top: 26px;
    color: var(--text-white);
  }
  .person-name {
    font-size: 38px;
    font-weight: 600;
    color: var(--name-blue);
    line-height: 1.1;
  }
  .divider {
    width: 130px;
    height: 2px;
    background: var(--rule-grey);
    margin: 10px 0 8px;
  }
  .quote-line {
    font-size: 29px;
    line-height: 1.32;
    text-align: center;
  }
  .phone-row {
    display: flex;
    align-items: center;
    gap: 8px;
    font-size: 30px;
    margin-top: 4px;
  }
  .phone-row svg { flex: none; }
  .phone-number { margin-right: 4px; }
  .services-band {
    flex: 1;
    background: linear-gradient(100deg, var(--band-light) 0%, var(--band-light) 55%, var(--band-deep) 100%);
    display: flex;
    align-items: center;
    justify-content: center;
    text-align: center;
    color: var(--text-white);
    font-size: 29px;
    line-height: 1.26;
    padding: 0 40px;
  }
</style>
</head>
<body>
<main class="canvas">
  <article class="business-card">
    <header class="card-header">
      <span class="brand-mark"></span>
      <span class="brand-name">KRV</span>
    </header>

    <section class="contact-panel">
      <h1 class="person-name">Lic. Mariela Torres Vidal</h1>
      <div class="divider"></div>
      <p class="quote-line">Cotizaciones en<br>tornilleriakrv.ventas@example.com</p>
      <div class="divider"></div>
      <p class="phone-row">
        <svg width="26" height="26" viewBox="0 0 24 24" aria-hidden="true">
          <path d="M6.6 10.8c1.4 2.8 3.8 5.1 6.6 6.6l2.2-2.2c.3-.3.7-.4 1-.2 1.1.4 2.3.6 3.6.6.6 0 1 .4 1 1V20c0 .6-.4 1-1 1C10.6 21 3 13.4 3 4c0-.6.4-1 1-1h3.5c.6 0 1 .4 1 1 0 1.2.2 2.4.6 3.6.1.3 0 .7-.2 1L6.6 10.8z" fill="none" stroke="#1a98dc" stroke-width="1.6"/>
        </svg>
        <span class="phone-number">5550142236</span>
        <svg width="20" height="28" viewBox="0 0 20 28" aria-hidden="true">
          <rect x="2" y="1.5" width="16" height="25" rx="2.5" fill="none" stroke="#1a98dc" stroke-width="2.4"/>
          <circle cx="10" cy="22.5" r="1.4" fill="#1a98dc"/>
        </svg>
        <span class="phone-number">5550198741</span>
      </p>
    </section>

    <footer class="services-band">
      <p>Custom Manufacture Any Size or Quantity Fastners for Large&nbsp; Mining<br>
      Equipment Trains, Ships, Green Energy Equipment<br>
      or Government Projects</p>
    </footer>
  </article>
</main>
</body>
</html>
```